borvant llc

excavating and landscaping

Target Market(s)

Industry/Entity Type

Contact Information for Business Card

file atach

Font styles to use
Serif

```html
<!DOCTYPE html>
<html lang="en">
<head>
<meta charset="utf-8">
<title>Borvant LLC business card</title>
<link rel="stylesheet" href="https://fonts.googleapis.com/css2?family=Rubik:wght@400;500;700&display=swap">
<style>
  :root {
    --stage: #e4e4e4;
    --card-white: #ffffff;
    --card-dark: #2b2b2d;
    --brand-red: #d61f26;
    --ink: #1c1c1c;
    --muted: #3a3a3a;
    --rule: #6d6d6d;
  }
  * { box-sizing: border-box; margin: 0; padding: 0; }
  html, body {
    width: 1200px; height: 801px; overflow: hidden;
    background: var(--stage);
    font-family: "Rubik", sans-serif;
  }
  .card {
    position: absolute; top: 240px;
    width: 560px; height: 320px;
    border-radius: 16px;
    overflow: hidden;
    border-bottom: 4px solid var(--brand-red);
    box-shadow: 0 6px 18px rgba(0,0,0,.18);
  }
  .card--back { left: 30px; background: var(--card-dark); }
  .card--front { left: 610px; background: var(--card-white); }

  .wordmark {
    display: flex; align-items: center; gap: 10px;
    font-weight: 700; letter-spacing: 1px; text-transform: uppercase;
    white-space: nowrap;
  }
  .wordmark__mark { width: 14px; height: 14px; background: var(--brand-red); flex: none; }
  .card--back .wordmark {
    position: absolute; left: 0; right: 0; top: 130px;
    justify-content: center; font-size: 44px; color: var(--brand-red);
  }
  .card--front .wordmark {
    position: absolute; left: 28px; top: 116px; width: 240px;
    font-size: 27px; color: var(--ink);
  }
  .card--front .wordmark__mark { width: 12px; height: 12px; }

  .divider {
    position: absolute; left: 292px; top: 40px;
    width: 1.5px; height: 160px; background: var(--rule);
  }
  .divider::after {
    content: ""; position: absolute; left: -0.5px; top: 40px;
    width: 2.5px; height: 70px; background: var(--brand-red);
  }

  .contact { position: absolute; left: 312px; top: 34px; color: var(--muted); }
  .contact__name { font-size: 23px; font-weight: 700; color: var(--brand-red); letter-spacing: .5px; }
  .contact__role { font-size: 13px; margin-top: 4px; }
  .contact__rule { width: 26px; height: 2px; background: var(--brand-red); margin: 6px 0; }
  .contact__line { font-size: 13px; line-height: 18px; }
  .contact__list { list-style: none; }
  .contact__list li { display: flex; align-items: center; gap: 7px; font-size: 13px; line-height: 19px; }
  .contact__list svg { width: 11px; height: 11px; fill: var(--brand-red); flex: none; }

  .tagline-band {
    position: absolute; left: 0; right: 0; top: 232px; height: 34px;
    background: var(--brand-red); color: #fff;
    display: flex; align-items: center; justify-content: center;
    font-weight: 700; font-size: 15px; letter-spacing: 1.5px; text-transform: uppercase;
  }
</style>
</head>
<body>
  <section class="card card--back" aria-label="Card back">
    <div class="wordmark"><span class="wordmark__mark"></span>Borvant LLC</div>
  </section>

  <section class="card card--front" aria-label="Card front">
    <div class="wordmark"><span class="wordmark__mark"></span>Borvant LLC</div>
    <div class="divider"></div>
    <div class="contact">
      <div class="contact__name">DALE MARROW</div>
      <div class="contact__role">Founder</div>
      <div class="contact__rule"></div>
      <div class="contact__line">48 Quarry Lane</div>
      <div class="contact__line">Millbrook, MA 01900</div>
      <div class="contact__rule"></div>
      <ul class="contact__list">
        <li><svg viewBox="0 0 24 24"><path d="M6.6 10.8a15 15 0 0 0 6.6 6.6l2.2-2.2a1 1 0 0 1 1-.25 11.4 11.4 0 0 0 3.6.6 1 1 0 0 1 1 1V20a1 1 0 0 1-1 1A17 17 0 0 1 3 4a1 1 0 0 1 1-1h3.5a1 1 0 0 1 1 1c0 1.25.2 2.45.6 3.6a1 1 0 0 1-.25 1z"/></svg>555-201-4873</li>
        <li><svg viewBox="0 0 24 24"><path d="M2 5h20v14H2z M2 5l10 8 10-8"/></svg>info@borvantllc.com</li>
        <li><svg viewBox="0 0 24 24"><circle cx="12" cy="12" r="10"/></svg>borvantllc.com</li>
      </ul>
    </div>
    <div class="tagline-band">Excavating and Landscaping</div>
  </section>
</body>
</html>
```